Banner ads for LP that work with same theme as below banners

Love the banner ads below. Need more with attached photos. But use the same wording, font as in below banner ads. Should be LP size 1200/627 so I can use for Pixorly and LP. Looking for great ads to use as LP ads. We do lots of ads so it will be worth your time to enter this contest you will be rewarded with a ton of work. Need several banner ads that work together. So maybe 1 of the dresses, 1 of the sweater, 1 of the leggings, 1 of the jacket

Target Market(s)

Women 24-45

Industry/Entity Type

Fashion

Requirements
Must have
• Banner ads that work for LP and Pixorly
Nice to have
• Several options to choose from
Should not have
• not sure

```html
<!DOCTYPE html>
<html lang="en">
<head>
<meta charset="UTF-8">
<title>Our Best Dresses Ever – Banner</title>
<link rel="stylesheet" href="https://fonts.googleapis.com/css2?family=Playball&family=Tinos:wght@400;700&display=swap">
<style>
  :root {
    --bg-dark: #1c1c1c;
    --bg-band: #262626;
    --bg-band-light: #2e2e2e;
    --frame-white: #f4f4f4;
    --script-white: #ffffff;
    --headline-grey: #cbc4c4;
    --button-bg: #eeeeee;
    --button-text: #1a1a1a;
    --photo-rust: #b5584a;
    --photo-red: #d23a3c;
    --photo-black: #2a2424;
    --photo-navy: #1f1c22;
    --photo-honey: #c58a55;
    --photo-beige: #b79c88;
  }
  * { box-sizing: border-box; margin: 0; padding: 0; }
  html, body { width: 1200px; height: 627px; overflow: hidden; background: var(--bg-dark); }
  .banner {
    position: relative;
    width: 1200px;
    height: 627px;
    overflow: hidden;
    background: var(--bg-dark);
  }
  .banner__texture { position: absolute; inset: 0; }
  .collage__item {
    position: absolute;
    background: var(--frame-white);
    padding: 6px;
    box-shadow: 0 4px 10px rgba(0,0,0,0.55);
  }
  .collage__photo { width: 100%; height: 100%; }
  .collage__item--one   { left: 48px;  top: 150px; width: 224px; height: 146px; transform: rotate(2deg); }
  .collage__item--two   { left: 290px; top: 258px; width: 220px; height: 150px; transform: rotate(-13deg); }
  .collage__item--three { left: 66px;  top: 296px; width: 226px; height: 162px; transform: rotate(-2deg); }
  .collage__item--four  { left: 88px;  top: 458px; width: 230px; height: 150px; transform: rotate(-2deg); }
  .collage__item--five  { left: 306px; top: 442px; width: 226px; height: 160px; transform: rotate(-2deg); }
  .collage__item--six   { left: 524px; top: 432px; width: 132px; height: 164px; transform: rotate(-2deg); }

  .photo--rust  { background: linear-gradient(160deg, #e3dfe2 0%, #cbb8b0 45%, var(--photo-rust) 100%); }
  .photo--red   { background: linear-gradient(170deg, #ededed 0%, #d9b39a 35%, var(--photo-red) 70%); }
  .photo--black { background: linear-gradient(170deg, #f2f2f2 0%, #b79478 40%, var(--photo-black) 85%); }
  .photo--navy  { background: linear-gradient(170deg, #f5f5f5 0%, #8a6a5c 40%, var(--photo-navy) 85%); }
  .photo--honey { background: linear-gradient(160deg, #d9d2cc 0%, var(--photo-honey) 50%, #5a3b2a 100%); }
  .photo--beige { background: linear-gradient(170deg, #f3f3f3 0%, #5a4038 40%, var(--photo-beige) 90%); }

  .headline {
    position: absolute;
    left: 660px;
    top: 70px;
    width: 430px;
    text-align: center;
  }
  .headline__script {
    display: block;
    font-family: "Playball", cursive;
    color: var(--script-white);
    font-size: 66px;
    line-height: 1;
  }
  .headline__script--top { margin-left: -20px; }
  .headline__script--bottom { font-size: 76px; margin-top: 8px; margin-left: -30px; }
  .headline__main {
    display: block;
    font-family: "Tinos", "Times New Roman", serif;
    font-weight: 700;
    font-size: 60px;
    letter-spacing: 0.36em;
    color: var(--headline-grey);
    margin-top: 18px;
    margin-right: -0.36em;
    line-height: 1;
  }
  .cta {
    position: absolute;
    left: 719px;
    top: 376px;
    width: 319px;
    height: 58px;
    background: var(--button-bg);
    color: var(--button-text);
    font-family: "Tinos", "Times New Roman", serif;
    font-size: 28px;
    display: flex;
    align-items: center;
    justify-content: center;
    text-decoration: none;
    letter-spacing: 0.01em;
  }
  .cta__strong { font-weight: 700; }
  .cta__light { font-weight: 400; margin: 0 0.25em; }
</style>
</head>
<body>
  <div class="banner">
    <svg class="banner__texture" width="1200" height="627" viewBox="0 0 1200 627" aria-hidden="true">
      <rect width="1200" height="627" fill="var(--bg-dark)"/>
      <polygon points="0,0 1200,0 1200,60 0,110" fill="var(--bg-band)"/>
      <polygon points="0,110 1200,60 1200,75 0,128" fill="var(--bg-band-light)" opacity="0.5"/>
      <polygon points="620,627 1200,300 1200,627" fill="var(--bg-band)" opacity="0.7"/>
      <polygon points="900,627 1200,450 1200,627" fill="var(--bg-band-light)" opacity="0.5"/>
    </svg>

    <div class="collage">
      <div class="collage__item collage__item--one"><div class="collage__photo photo--rust" role="img" aria-label="Model in a rust lace-up knit top"></div></div>
      <div class="collage__item collage__item--two"><div class="collage__photo photo--red" role="img" aria-label="Model in a red lace dress with sunflower embroidery"></div></div>
      <div class="collage__item collage__item--three"><div class="collage__photo photo--black" role="img" aria-label="Model in a black lace-shoulder dress"></div></div>
      <div class="collage__item collage__item--four"><div class="collage__photo photo--navy" role="img" aria-label="Model in a dark dress with floral embroidered neckline"></div></div>
      <div class="collage__item collage__item--five"><div class="collage__photo photo--honey" role="img" aria-label="Model in a patterned sequin dress"></div></div>
      <div class="collage__item collage__item--six"><div class="collage__photo photo--beige" role="img" aria-label="Model in a nude embellished dress"></div></div>
    </div>

    <h1 class="headline">
      <span class="headline__script headline__script--top">Our Best</span>
      <span class="headline__main">DRESSES</span>
      <span class="headline__script headline__script--bottom">Ever!</span>
    </h1>

    <a class="cta" href="#"><span class="cta__strong">SHOP</span><span class="cta__light">THE</span><span class="cta__strong">LOOK</span></a>
  </div>
</body>
</html>
```